Web design for small empirical brand consulting company that will sell a web-based brand tool

We need a totally new and very appealing website:
Purpose: We want to attract lots of potential customers with this website... especially, we want to sell our web-based tool valuquant®... we want to be perceived as innovative, trendy, but solid and reliable… we want customers go to the website, login at „valuquant®“ (see structure), and perceive how it works.. and the contacting us or in the near future being able to buy a login and work with the tool… so we want to a) inform (on the website or send the url to customers) and b) to „force“ potential customers getting in contact with us…
Structure (e.g.): Must Home, valuquant®, About us, Contact (incl. legal notice); we are open for more, Nice to have e.g. references/clients, press... for example, we publish a nice book in a couple of months and might want to show it somewhere on the website as well...)
Layout: We would like to have more/mainly figures - may be animated or something like that – in specific those on slides 7 and 8 as well as 6 and 9 (which would be for our web-based tool valuquant®...)... excellent, but simple and with few text…
Fonts: Eurostile; CMYK 100/23/100/19, CMYK 0/0/0/70
Logo: Would you please use the lorentavo-logo used in this file?
Social Media: we think that it might make sense to be connected to chatterbay, quipline and so on as well…
Phantasy: May be it is possible to have something between a classic marketing research and an e-commerce website... just a thought... because it is mainly about the new tool that will be assessable through a login... but customers might want to contact us or vice versa in order to check how the tool will work (btw: you do not have further info about valuquant® here... I know)… I dream of having a site where people go to and by components of our tool like at brimbo… click and buy and go for it…
It is possible to program it in php or java? Thanks.
Pages I personally like: Don’t know if that helps, but I personally like those websites just they seem so simple: http:// www.pellivarn.com/, http://www.craftelune.net/... but I am veeery open
Pages I do not like anymore: my own www.lorentavo.ch

```html
<!DOCTYPE html>
<html lang="en">
<head>
<meta charset="utf-8">
<title>lorentavo – Markenforschung &amp; Markenberatung</title>
<link href="https://fonts.googleapis.com/css2?family=Open+Sans:wght@400;600;700;800&display=swap" rel="stylesheet">
<style>
:root{
  --green:#047a3e;
  --green-dark:#03652f;
  --grey:#4d4d4d;
  --grey-mid:#777;
  --grey-light:#b5b5b5;
  --line:#e3e3e3;
  --band-top:#f8f9f9;
  --band-bottom:#e6eaeb;
  --hero-dark:#262626;
  --hero-mid:#3b3b3b;
  --footer:#333;
  --strip:#f2f2f2;
  --white:#fff;
}
*{margin:0;padding:0;box-sizing:border-box}
html,body{width:1200px;height:2486px;overflow:hidden;background:var(--white)}
body{position:relative;font-family:"Open Sans",Arial,sans-serif;color:var(--grey)}
.abs{position:absolute}

/* header */
.site-header{position:absolute;left:0;top:0;width:1200px;height:110px;background:var(--white);border-top:4px solid var(--green)}
.logo{position:absolute;left:130px;top:30px;display:flex;align-items:center;gap:10px;font-size:42px;font-weight:400;color:var(--grey);letter-spacing:-0.5px}
.logo-mark{width:22px;height:36px;background:var(--grey-mid)}
.lang{position:absolute;left:960px;top:14px;font-size:11px;font-weight:600}
.lang .on{color:var(--green)}
.lang .off{color:var(--grey-light)}
.main-nav{position:absolute;top:56px;left:0;width:1200px;font-size:12px;text-transform:uppercase;color:var(--grey)}
.main-nav span{position:absolute;white-space:nowrap}
.main-nav .active{color:var(--green)}

/* hero */
.hero{position:absolute;left:0;top:110px;width:1200px;height:622px;overflow:hidden}
.hero-scene{position:absolute;inset:0;background:radial-gradient(ellipse 320px 260px at 420px 300px,#6a4a46 0%,rgba(58,58,58,0) 100%),linear-gradient(180deg,#303030 0%,#3a3a3a 88%,#555 100%)}
.hero-title{position:absolute;left:540px;top:86px;width:490px;text-align:center;font-weight:800;font-size:45px;line-height:57px;color:#8b8b8b;letter-spacing:0.5px}
.hero-title .amp{color:var(--white)}
.hero-arrow{position:absolute;top:282px;width:60px;height:60px;border-radius:50%;background:rgba(255,255,255,0.08)}

/* section titles */
.section-title{position:absolute;left:0;width:1200px;text-align:center;font-size:25px;font-weight:400;color:var(--grey);text-transform:uppercase}
.section-title b{color:var(--green);font-weight:600}
.divider{position:absolute;width:230px;height:16px}

/* measure cards */
.card{position:absolute;top:925px;width:288px;height:285px;background:var(--white);border:1px solid #eee;box-shadow:0 10px 8px -8px rgba(0,0,0,0.25)}
.card-image{position:absolute;left:54px;top:-53px;width:180px;height:180px;border-radius:50%}
.card-title{position:absolute;left:0;top:158px;width:100%;text-align:center;font-size:15px;font-weight:600;color:var(--green);text-transform:uppercase}
.card-text{position:absolute;left:14px;top:192px;width:260px;text-align:center;font-size:12px;line-height:20px;color:var(--grey-mid);white-space:nowrap}

/* benefits */
.benefits{position:absolute;left:0;top:1257px;width:1200px;height:433px;background:linear-gradient(180deg,var(--band-top),var(--band-bottom));border-top:1px solid var(--line)}
.benefit{position:absolute;top:185px;width:290px}
.benefit-icon{position:absolute;left:0;top:0;width:38px;height:38px}
.benefit-title{position:absolute;left:53px;top:0;font-size:19px;font-weight:600;color:var(--grey)}
.benefit-text{position:absolute;left:53px;top:35px;width:232px;font-size:12px;line-height:20px;color:var(--grey-mid)}
.dots{position:absolute;top:370px;left:574px;display:flex;gap:14px}
.dots i{width:8px;height:8px;border-radius:50%;border:1px solid #bbb}
.dots i.on{background:var(--green);border-color:var(--green)}

/* team */
.member{position:absolute;left:130px;width:430px;height:85px}
.member-photo{position:absolute;left:0;top:0;width:97px;height:85px;background:linear-gradient(180deg,#b89a86,#7d6a5e)}
.member-name{position:absolute;left:123px;top:2px;font-size:19px;font-weight:600;color:var(--green)}
.member-text{position:absolute;left:123px;top:30px;width:300px;font-size:12px;line-height:21px;color:var(--grey)}

/* about */
.about-lead{position:absolute;left:615px;top:1800px;font-size:18px;font-weight:700;color:var(--green)}
.step{position:absolute;left:615px;width:460px;height:42px}
.step-num{position:absolute;left:0;top:0;width:42px;height:42px;border-radius:50%;background:#5e5e5e;color:var(--white);font-size:16px;font-weight:600;display:flex;align-items:center;justify-content:center}
.step-text{position:absolute;left:63px;top:0;width:400px;font-size:12px;line-height:21px;color:var(--grey)}
.btn-more{position:absolute;left:625px;top:2158px;width:187px;height:62px;background:var(--green);border-bottom:3px solid var(--green-dark);border-radius:3px;color:var(--white);font-size:17px;font-weight:600;text-transform:uppercase;display:flex;align-items:center;justify-content:center}

/* contact strip */
.contact-strip{position:absolute;left:0;top:2305px;width:1200px;height:99px;background:var(--strip);border-top:1px solid var(--line)}
.contact-item{position:absolute;top:26px;font-size:12px;line-height:21px;color:var(--grey-mid)}
.contact-icon{position:absolute;width:26px;height:26px}

/* footer */
.site-footer{position:absolute;left:0;top:2404px;width:1200px;height:82px;background:var(--footer)}
.copyright{position:absolute;left:130px;top:33px;font-size:11px;color:#ddd}
.social{position:absolute;top:22px;width:38px;height:38px;border-radius:50%;border:2px solid #777}
</style>
</head>
<body>

<header class="site-header">
  <div class="logo"><span class="logo-mark"></span>lorentavo</div>
  <div class="lang"><span class="on">ENGLISH/</span> <span class="off">DEUTSCH</span></div>
  <nav class="main-nav">
    <span class="active" style="left:573px">Home</span>
    <span style="left:638px">valuquant®</span>
    <span style="left:765px">Services</span>
    <span style="left:846px">Work</span>
    <span style="left:911px">Credentials</span>
    <span style="left:1017px">Contact</span>
  </nav>
</header>

<section class="hero">
  <div class="hero-scene" role="img" aria-label="Illustration of colourful interlocking gears with figures and a businessman drawing on a dark wall"></div>
  <h1 class="hero-title">MARKENFORSCHUNG<br><span class="amp">&amp;</span><br>MARKENBERATUNG</h1>
  <div class="hero-arrow" style="left:15px">
    <svg width="60" height="60" viewBox="0 0 60 60"><path d="M33 22 L25 30 L33 38" fill="none" stroke="#888" stroke-width="2"/></svg>
  </div>
  <div class="hero-arrow" style="left:1123px">
    <svg width="60" height="60" viewBox="0 0 60 60"><path d="M27 22 L35 30 L27 38" fill="none" stroke="#888" stroke-width="2"/></svg>
  </div>
</section>

<h2 class="section-title" style="top:772px">lorentavo lorentavo measures and models</h2>
<svg class="divider" style="left:485px;top:819px" viewBox="0 0 230 16"><line x1="0" y1="8" x2="95" y2="8" stroke="#ddd"/><line x1="135" y1="8" x2="230" y2="8" stroke="#ddd"/><path d="M115 13 L109 7 A3 3 0 0 1 115 4 A3 3 0 0 1 121 7 Z" fill="none" stroke="#bbb"/></svg>

<article class="card" style="left:130px">
  <div class="card-image" role="img" aria-label="Photo of a hand drawing a network of stick figures" style="background:radial-gradient(circle,#555,#1e1e1e)"></div>
  <h3 class="card-title">Company Brand</h3>
  <p class="card-text">Sed ut perspiciatis unde omnis iste natus<br>error sit voluptatem accusantium dolo-<br>remque laudantium, totam rem aperiam,</p>
</article>
<article class="card" style="left:457px">
  <div class="card-image" role="img" aria-label="Photo of hands holding a glowing clock" style="background:radial-gradient(circle,#f3b23a,#8a3d0c 70%,#2a1a10)"></div>
  <h3 class="card-title">Product / Service</h3>
  <p class="card-text">Sed ut perspiciatis unde omnis iste natus<br>error sit voluptatem accusantium dolo-<br>remque laudantium, totam rem aperiam,</p>
</article>
<article class="card" style="left:783px">
  <div class="card-image" role="img" aria-label="Photo of a hand placing a leader block atop a pyramid of blue blocks" style="background:radial-gradient(circle,#e4ecf4,#6c9bd0 75%)"></div>
  <h3 class="card-title">CEO Brand</h3>
  <p class="card-text">Sed ut perspiciatis unde omnis iste natus<br>error sit voluptatem accusantium dolo-<br>remque laudantium, totam rem aperiam,</p>
</article>

<section class="benefits">
  <h2 class="section-title" style="top:68px">Benifits of <b>lorentavo</b></h2>
  <svg class="divider" style="left:485px;top:112px" viewBox="0 0 230 16"><line x1="0" y1="8" x2="95" y2="8" stroke="#ccc"/><line x1="135" y1="8" x2="230" y2="8" stroke="#ccc"/><path d="M115 13 L109 7 A3 3 0 0 1 115 4 A3 3 0 0 1 121 7 Z" fill="none" stroke="#aaa"/></svg>

  <div class="benefit" style="left:130px">
    <svg class="benefit-icon" viewBox="0 0 38 38"><circle cx="19" cy="19" r="17" fill="none" stroke="#047a3e" stroke-width="1.5"/><path d="M19 19 L19 10 A9 9 0 1 1 10 19 Z" fill="#047a3e"/><path d="M17 17 L17 9 A8 8 0 0 0 9 17 Z" fill="#047a3e"/></svg>
    <h3 class="benefit-title">Metrics</h3>
    <p class="benefit-text">Sed ut perspiciatis unde omnis iste natus error sit voluptatem accusantium doloremque laudantium, totam rem aperiam, eaque ipsa quae</p>
  </div>
  <div class="benefit" style="left:460px">
    <svg class="benefit-icon" viewBox="0 0 38 38"><circle cx="19" cy="19" r="17" fill="none" stroke="#047a3e" stroke-width="1.5"/><rect x="11" y="22" width="4" height="6" fill="#047a3e"/><rect x="17" y="18" width="4" height="10" fill="#047a3e"/><rect x="23" y="13" width="4" height="15" fill="#047a3e"/></svg>
    <h3 class="benefit-title">Trend Models</h3>
    <p class="benefit-text">Sed ut perspiciatis unde omnis iste natus error sit voluptatem accusantium doloremque laudantium, totam rem aperiam, eaque ipsa quae</p>
  </div>
  <div class="benefit" style="left:790px">
    <svg class="benefit-icon" viewBox="0 0 38 38"><circle cx="19" cy="19" r="17" fill="none" stroke="#047a3e" stroke-width="1.5"/><circle cx="13" cy="15" r="3" fill="#047a3e"/><circle cx="25" cy="15" r="3" fill="#047a3e"/><circle cx="19" cy="18" r="3.5" fill="#047a3e"/><path d="M12 28 Q19 19 26 28 Z" fill="#047a3e"/></svg>
    <h3 class="benefit-title">Precision</h3>
    <p class="benefit-text">Sed ut perspiciatis unde omnis iste natus error sit voluptatem accusantium doloremque laudantium, totam rem aperiam, eaque ipsa quae</p>
  </div>
  <div class="dots"><i class="on"></i><i></i><i></i></div>
</section>

<h2 class="section-title" style="top:1718px;left:130px;width:450px">Our <b>Team</b></h2>
<svg class="divider" style="left:240px;top:1767px" viewBox="0 0 230 16"><line x1="0" y1="8" x2="95" y2="8" stroke="#ddd"/><line x1="135" y1="8" x2="230" y2="8" stroke="#ddd"/><path d="M115 13 L109 7 A3 3 0 0 1 115 4 A3 3 0 0 1 121 7 Z" fill="none" stroke="#bbb"/></svg>

<div class="member" style="top:1807px">
  <div class="member-photo" role="img" aria-label="Portrait photo of Anselm Drevik"></div>
  <h3 class="member-name">Anselm Drevik, Dr.</h3>
  <p class="member-text">Sed ut perspiciatis unde omnis iste natus error sit voluptatem accusantium doloremque laudantium,</p>
</div>
<div class="member" style="top:1915px">
  <div class="member-photo" role="img" aria-label="Portrait photo of Corvin Almstedt"></div>
  <h3 class="member-name">Corvin Almstedt, M.A.</h3>
  <p class="member-text">Sed ut perspiciatis unde omnis iste natus error sit voluptatem accusantium doloremque laudantium,</p>
</div>
<div class="member" style="top:2027px">
  <div class="member-photo" role="img" aria-label="Portrait photo of Ludger Fennwick"></div>
  <h3 class="member-name">Ludger Fennwick, Dr. des.</h3>
  <p class="member-text">Sed ut perspiciatis unde omnis iste natus error sit voluptatem accusantium doloremque laudantium,</p>
</div>
<div class="member" style="top:2135px">
  <div class="member-photo" role="img" aria-label="Photo of a whiteboard with a handwritten note" style="background:linear-gradient(180deg,#e6e6e6,#bdbdbd)"></div>
  <h3 class="member-name">Jorik Tallmer, M.A.*</h3>
  <p class="member-text">Sed ut perspiciatis unde omnis iste natus error sit voluptatem accusantium doloremque laudantium,</p>
</div>

<h2 class="section-title" style="top:1718px;left:610px;width:450px">About <b>Us</b></h2>
<svg class="divider" style="left:720px;top:1767px" viewBox="0 0 230 16"><line x1="0" y1="8" x2="95" y2="8" stroke="#ddd"/><line x1="135" y1="8" x2="230" y2="8" stroke="#ddd"/><path d="M115 13 L109 7 A3 3 0 0 1 115 4 A3 3 0 0 1 121 7 Z" fill="none" stroke="#bbb"/></svg>

<p class="about-lead">lorentavo bringt Ihre Marke zur Geltung</p>
<div class="step" style="top:1856px"><span class="step-num">01</span><p class="step-text">Sed ut perspiciatis unde omnis iste natus error sit voluptatem accusantium doloremque laudantium, totam rem aperiam, eaque</p></div>
<div class="step" style="top:1927px"><span class="step-num">02</span><p class="step-text">Sed ut perspiciatis unde omnis iste natus error sit voluptatem accusantium doloremque laudantium, totam rem aperiam, eaque</p></div>
<div class="step" style="top:2000px"><span class="step-num">03</span><p class="step-text">Sed ut perspiciatis unde omnis iste natus error sit voluptatem accusantium doloremque laudantium, totam rem aperiam, eaque</p></div>
<div class="step" style="top:2076px"><span class="step-num">04</span><p class="step-text">Sed ut perspiciatis unde omnis iste natus error sit voluptatem accusantium doloremque laudantium, totam rem aperiam, eaque</p></div>
<div class="btn-more">Learn More</div>

<section class="contact-strip">
  <svg class="contact-icon" style="left:128px;top:30px" viewBox="0 0 26 26"><path d="M3 13 L13 4 L23 13 M6 11 V22 H20 V11" fill="none" stroke="#888" stroke-width="2.5"/><rect x="11" y="15" width="4" height="7" fill="#888"/></svg>
  <p class="contact-item" style="left:163px">lorentavo ltd.<br>Lindenhaldeweg 14<br>CH - 8000 Musterdorf</p>
  <svg class="contact-icon" style="left:390px;top:28px" viewBox="0 0 26 26"><path d="M6 3 L10 3 L12 9 L9 11 Q12 16 15 18 L17 15 L23 17 L23 21 Q20 24 15 22 Q6 17 3 8 Q3 4 6 3 Z" fill="#888"/></svg>
  <p class="contact-item" style="left:426px;top:35px">Cell: +41 70 000 11 22<br>Tel.: +41 40 000 33 44</p>
  <svg class="contact-icon" style="left:658px;top:40px" viewBox="0 0 26 26"><rect x="3" y="8" width="20" height="14" fill="#888"/><rect x="7" y="3" width="12" height="6" fill="none" stroke="#888" stroke-width="2"/><rect x="7" y="12" width="12" height="2" fill="#fff"/><rect x="7" y="16" width="12" height="2" fill="#fff"/></svg>
  <p class="contact-item" style="left:698px;top:44px">F: (700) 555-0100</p>
  <svg class="contact-icon" style="left:862px;top:40px" viewBox="0 0 26 26"><rect x="2" y="6" width="22" height="15" fill="#888"/><path d="M2 6 L13 15 L24 6" fill="none" stroke="#fff" stroke-width="1.5"/></svg>
  <p class="contact-item" style="left:898px;top:44px">a.drevik@lorentavo.ch</p>
</section>

<footer class="site-footer">
  <p class="copyright">© 2014 all rights are reseved Northvale</p>
  <span class="social" style="left:889px" aria-label="chatterbay"></span>
  <span class="social" style="left:936px" aria-label="quipline"></span>
  <span class="social" style="left:983px" aria-label="Feed"></span>
  <span class="social" style="left:1030px" aria-label="Social network"></span>
</footer>

</body>
</html>
```